Moravel Aesthetic Doctor

I require an elegant, luxurious looking business card for my aesthetic business. I am a doctor and that will set me aside from competitors. I am planning to provide home and spa based treatments to clients with high expectations. I have attached my logo.

```html
<!DOCTYPE html>
<html lang="en">
<head>
<meta charset="utf-8">
<title>Moravel Aesthetic Doctor – Business Card</title>
<link rel="stylesheet" href="https://fonts.googleapis.com/css2?family=Roboto:wght@300;400;500&display=swap">
<style>
  :root {
    --backdrop: #d6d6d6;
    --card-white: #ffffff;
    --ink-grey: #8e9195;
    --band-grey: #a9abad;
    --sky: #5bbde8;
    --sky-soft: #a9def3;
    --steel: #b4b7ba;
    --text-white: #ffffff;
  }
  html, body {
    margin: 0;
    width: 1125px;
    height: 1200px;
    overflow: hidden;
    background: var(--backdrop);
    font-family: "Roboto", sans-serif;
  }
  .card {
    position: absolute;
    left: 151px;
    width: 799px;
    height: 457px;
    border-radius: 22px;
    overflow: hidden;
    transform: scale(1.032);
    transform-origin: top left;
    box-shadow: 0 4px 10px rgba(0,0,0,0.25);
  }
  .card-front { top: 98px; background: var(--card-white); }
  .card-back {
    top: 632px;
    background: linear-gradient(180deg, var(--sky-soft) 0%, var(--steel) 40%, var(--steel) 65%, var(--sky-soft) 100%);
  }
  .front-band { position: absolute; inset: 0; width: 100%; height: 100%; }
  .brand-name {
    position: absolute;
    left: 48px;
    top: 36px;
    margin: 0;
    color: var(--ink-grey);
    font-weight: 300;
    line-height: 1;
  }
  .brand-name .word { display: block; font-size: 58px; letter-spacing: 2px; }
  .brand-name .sub { display: block; font-size: 25px; letter-spacing: 2px; margin-top: 6px; }
  .doctor-name {
    position: absolute;
    left: 49px;
    top: 220px;
    margin: 0;
    color: var(--sky);
    font-size: 28px;
    font-weight: 400;
  }
  .doctor-name .letters { font-size: 19px; }
  .credential {
    position: absolute;
    left: 49px;
    top: 259px;
    margin: 0;
    color: var(--ink-grey);
    font-size: 20px;
    font-weight: 300;
  }
  .contact-list {
    position: absolute;
    left: 49px;
    top: 304px;
    margin: 0;
    padding: 0;
    list-style: none;
    color: var(--ink-grey);
    font-size: 21px;
    font-weight: 300;
  }
  .contact-list li { display: flex; align-items: center; height: 32px; }
  .contact-list svg { width: 18px; height: 18px; margin-right: 13px; }
  .contact-list .accent { color: var(--sky); }
  .social-dots { position: absolute; left: 295px; top: 372px; display: flex; gap: 20px; }
  .social-dots span { width: 26px; height: 26px; border-radius: 50%; background: var(--sky); }
  .back-brand {
    position: absolute;
    left: 0; right: 0;
    top: 130px;
    display: flex;
    justify-content: center;
    align-items: center;
    gap: 26px;
  }
  .back-brand .ring {
    width: 116px; height: 116px;
    border-radius: 50%;
    border: 4px solid var(--text-white);
    box-sizing: border-box;
  }
  .back-brand .name {
    margin: 0;
    color: var(--text-white);
    font-weight: 300;
    line-height: 1;
  }
  .back-brand .word { display: block; font-size: 74px; letter-spacing: 3px; }
  .back-brand .sub { display: block; font-size: 30px; letter-spacing: 3px; margin-top: 8px; }
  .services {
    position: absolute;
    left: 0; right: 0;
    top: 314px;
    margin: 0;
    text-align: center;
    color: var(--text-white);
    font-size: 21px;
    font-weight: 300;
    line-height: 32px;
  }
</style>
</head>
<body>
  <section class="card card-front">
    <svg class="front-band" viewBox="0 0 799 457" preserveAspectRatio="none" aria-hidden="true">
      <path d="M0,410 Q400,455 799,382 L799,457 L0,457 Z" fill="var(--band-grey)"/>
      <path d="M0,410 Q400,450 799,372 L799,382 Q400,455 0,410 Z" fill="var(--card-white)"/>
      <path d="M230,437 Q560,428 799,360 L799,376 Q560,440 230,437 Z" fill="var(--sky)"/>
    </svg>
    <h1 class="brand-name"><span class="word">MORAVEL</span><span class="sub">AESTHETIC DOCTOR</span></h1>
    <p class="doctor-name">Dr Lena Marsh, <span class="letters">MRCPCH MD</span></p>
    <p class="credential">Australasian Diploma of Aesthetic Medicine</p>
    <ul class="contact-list">
      <li>
        <svg viewBox="0 0 24 24" aria-hidden="true"><path d="M6.6 10.8a15 15 0 0 0 6.6 6.6l2.2-2.2a1 1 0 0 1 1-.25 11.4 11.4 0 0 0 3.6.57 1 1 0 0 1 1 1V20a1 1 0 0 1-1 1A17 17 0 0 1 3 4a1 1 0 0 1 1-1h3.5a1 1 0 0 1 1 1c0 1.25.2 2.45.57 3.6a1 1 0 0 1-.25 1z" fill="var(--sky)"/></svg>
        0800 437 915
      </li>
      <li>
        <svg viewBox="0 0 24 24" aria-hidden="true"><rect x="3" y="6" width="18" height="13" rx="1" fill="none" stroke="var(--sky)" stroke-width="2"/><path d="M3 7l9 6 9-6" fill="none" stroke="var(--sky)" stroke-width="2"/></svg>
        lena@moravel.co.nz
      </li>
      <li>
        <svg viewBox="0 0 24 24" aria-hidden="true"><g fill="none" stroke="var(--sky)" stroke-width="1.6"><circle cx="12" cy="12" r="9"/><ellipse cx="12" cy="12" rx="4" ry="9"/><path d="M3 12h18M5 7h14M5 17h14"/></g></svg>
        www.<span class="accent">moravel</span>.co.nz
      </li>
    </ul>
    <div class="social-dots" aria-hidden="true"><span></span><span></span></div>
  </section>

  <section class="card card-back">
    <div class="back-brand">
      <div class="ring" aria-hidden="true"></div>
      <h2 class="name"><span class="word">MORAVEL</span><span class="sub">AESTHETIC DOCTOR</span></h2>
    </div>
    <p class="services">
      Dermal injectables • Plasma facials • Microneedling<br>
      Skin boosters • Excessive sweating<br>
      Home and Spa Based Treatments
    </p>
  </section>
</body>
</html>
```